Business Cards

Need business card design that I can update for new employees and details. Needs to incorporate our logo, be bright and fun (in line with tourism and holidays)
Would like a Map of Western Australia on the front with locations all the caravan parks we own (just purchased Tom Price so please include that as well as others listed on our website).
Target Market(s)
Famillies
Contact Information for Business Card
5 Cards -
Neil Perrow (Director) e: perrow@wattlebay.com.au p: 0491 570 156
Mira Perrow (Director) e: perrow@wattlebay.com.au p: 0491 570 157
Owen Halvey (General Manager) e: halvey@wattlebay.com.au p: 0491 570 158
Helen Halvey (General Manager) e: halvey@wattlebay.com.au p: 0491 570 159
Colin Danby (Training and Operations Manager) - e: danby@wattlebay.com.au p:0491 570 110
Colors
Look and feel

```html
<!DOCTYPE html>
<html lang="en">
<head>
<meta charset="utf-8">
<title>Wattle Bay Tourist Parks – Business Card</title>
<link rel="stylesheet" href="https://fonts.googleapis.com/css2?family=EB+Garamond:wght@400&family=Tinos:wght@400;700&display=swap">
<style>
  :root {
    --stage: #000000;
    --card-light: #f2f2f2;
    --card-teal: #3ab1ba;
    --teal-soft: #58c2c4;
    --accent: #3eb4bc;
    --ink: #1c1c1c;
    --wordmark-grey: #4d4d4d;
    --white: #ffffff;
  }
  * { margin: 0; padding: 0; box-sizing: border-box; }
  html, body {
    width: 1200px;
    height: 900px;
    overflow: hidden;
    background: var(--stage);
  }
  .stage {
    position: relative;
    width: 1200px;
    height: 900px;
  }
  .card {
    position: absolute;
    top: 200px;
    width: 310px;
    height: 502px;
    overflow: hidden;
  }
  .card--front {
    left: 278px;
    background: var(--card-light);
    border-radius: 72px 0 72px 0;
  }
  .card--back {
    left: 629px;
    width: 309px;
    background: var(--card-teal);
    border-radius: 0 72px 0 72px;
  }

  /* brand block */
  .brand {
    position: absolute;
    left: 0;
    right: 0;
    text-align: center;
    font-family: "EB Garamond", Georgia, serif;
    font-weight: 400;
  }
  .brand__mark {
    display: block;
    width: 78px;
    height: 78px;
    margin: 0 auto 6px;
    background: var(--accent);
  }
  .brand__name {
    display: block;
    font-size: 34px;
    letter-spacing: 3px;
    line-height: 1;
    text-transform: uppercase;
  }
  .brand__tagline {
    display: block;
    margin-top: 6px;
    font-size: 14px;
    letter-spacing: 3px;
    text-transform: uppercase;
  }
  .card--front .brand {
    top: 60px;
    color: var(--wordmark-grey);
  }
  .card--back .brand {
    top: 390px;
    color: var(--white);
  }

  /* back decoration area */
  .back-art {
    position: absolute;
    left: 0;
    top: 40px;
    width: 309px;
    height: 330px;
    background: radial-gradient(ellipse at 55% 55%, var(--teal-soft) 0%, rgba(88,194,196,0) 70%);
  }

  /* contact details */
  .contact {
    position: absolute;
    left: 25px;
    top: 356px;
    font-family: "Tinos", "Times New Roman", serif;
    color: var(--ink);
  }
  .contact__name {
    font-size: 19px;
    font-weight: 700;
    color: var(--accent);
    line-height: 1.1;
  }
  .contact__role {
    margin-top: 6px;
    font-size: 14px;
  }
  .contact__list {
    list-style: none;
    margin-top: 30px;
    font-size: 14px;
  }
  .contact__list li {
    display: flex;
    align-items: center;
    gap: 4px;
    height: 22px;
  }
  .contact__icon {
    width: 10px;
    height: 10px;
    fill: var(--accent);
    flex: none;
  }
</style>
</head>
<body>
<main class="stage">

  <section class="card card--front" aria-label="Card front">
    <div class="brand">
      <span class="brand__mark" aria-hidden="true"></span>
      <span class="brand__name">Wattle Bay</span>
      <span class="brand__tagline">Tourist Parks</span>
    </div>

    <div class="contact">
      <p class="contact__name">Neil Perrow</p>
      <p class="contact__role">Director</p>
      <ul class="contact__list">
        <li>
          <svg class="contact__icon" viewBox="0 0 10 10" aria-hidden="true">
            <path d="M2.1 0.4 L3.6 2.3 L2.7 3.4 C3.3 4.7 5.1 6.6 6.6 7.3 L7.7 6.4 L9.6 7.9 L8.6 9.5 C4.6 9.4 0.6 5.4 0.5 1.4 Z"/>
          </svg>
          <span>0491 570 156</span>
        </li>
        <li>
          <svg class="contact__icon" viewBox="0 0 10 10" aria-hidden="true">
            <path d="M0.5 2 H9.5 V8 H0.5 Z M1.2 2.6 L5 5.4 L8.8 2.6" stroke="#f2f2f2" stroke-width="0.7"/>
          </svg>
          <span>perrow@wattlebay.com.au</span>
        </li>
      </ul>
    </div>
  </section>

  <section class="card card--back" aria-label="Card back">
    <div class="back-art" role="img" aria-label="Large faint brand emblem decoration in light teal"></div>
    <div class="brand">
      <span class="brand__name">Wattle Bay</span>
      <span class="brand__tagline">Tourist Parks</span>
    </div>
  </section>

</main>
</body>
</html>
```